Healthcare and Professional IT Services Company need a redesigned business card

We are a IT Services company that targets small medical practices and professional business such as Attorneys, Accounts, Architects etc. We want to communicate a professional yet friendly image using recent logo redesign here on ArtHarbor. Like to see the colors blue and orange in the design. Must use the Tall Pine Computing as displayed in the new logo - then also want to incorporate the fish logo as well.

Target Market(s)

Small medical and professional services

Industry/Entity Type

It Company

Contact Information for Business Card

The usual stuff, place for name address phone website. Also maybe our tagline which is "hooked on technology"

Requirements
Must have
• My new logo and the fish somewhere on the card

```html
<!DOCTYPE html>
<html lang="en">
<head>
<meta charset="utf-8">
<title>Tall Pine Computing – Business Card</title>
<link rel="stylesheet" href="https://fonts.googleapis.com/css2?family=Open+Sans:wght@400;600&display=swap">
<style>
  :root {
    --page: #e4e4e4;
    --card: #000000;
    --wave: #56bce3;
    --brand-blue: #4a9fd6;
    --fish-blue: #3a8fc9;
    --fish-orange: #e27a3a;
    --ink-light: #ececec;
    --icon-bg: #f2f2f2;
  }
  * { margin: 0; padding: 0; box-sizing: border-box; }
  html, body {
    width: 1189px; height: 1200px; overflow: hidden;
    background: var(--page);
    font-family: "Open Sans", sans-serif;
  }
  .canvas { position: relative; width: 1189px; height: 1200px; }
  .card {
    position: absolute; left: 140px; width: 918px; height: 522px;
    background: var(--card); overflow: hidden;
  }
  .card--front { top: 47px; }
  .card--back { top: 624px; }

  .fish-mark {
    position: absolute; width: 189px; height: 131px;
    border-radius: 50%;
    background: radial-gradient(ellipse at 60% 50%, var(--fish-blue) 0%, #2d6fa8 55%, var(--fish-orange) 100%);
  }
  .brand-name {
    position: absolute; white-space: nowrap;
    font-weight: 600; color: var(--brand-blue);
    letter-spacing: -0.5px;
  }
  .card--front .fish-mark { left: 144px; top: 100px; }
  .card--front .brand-name { left: 343px; top: 126px; font-size: 47px; }
  .card--back .fish-mark { left: 129px; top: 216px; }
  .card--back .brand-name { left: 328px; top: 242px; font-size: 47px; }

  .wave { position: absolute; left: 0; top: 0; }

  .holder-name {
    position: absolute; left: 64px; top: 394px;
    font-size: 46px; color: var(--ink-light); white-space: nowrap;
  }
  .divider {
    position: absolute; left: 459px; top: 370px;
    width: 2px; height: 130px; background: var(--ink-light);
  }
  .contact-list { position: absolute; left: 481px; top: 383px; list-style: none; }
  .contact-list li {
    display: flex; align-items: center; height: 35px;
    font-size: 26px; color: var(--ink-light); white-space: nowrap;
  }
  .contact-list svg { width: 20px; height: 20px; margin-right: 24px; flex: none; }
</style>
</head>
<body>
<div class="canvas">

  <section class="card card--front">
    <div class="fish-mark" role="img" aria-label="Cartoon fish mascot illustration"></div>
    <div class="brand-name">Tall Pine Computing</div>

    <svg class="wave" width="918" height="522" viewBox="0 0 918 522" aria-hidden="true">
      <path d="M0 299 C160 330 300 345 450 318 C570 296 650 255 740 265 C820 274 880 305 918 333
               L918 330 C870 300 810 276 740 272 C650 268 580 315 450 345 C300 378 150 368 0 345 Z"
            fill="var(--wave)"/>
    </svg>

    <div class="holder-name">Daniel Whitmore</div>
    <div class="divider"></div>
    <ul class="contact-list">
      <li>
        <svg viewBox="0 0 20 20" aria-hidden="true"><rect width="20" height="20" fill="var(--icon-bg)"/>
          <path d="M6 4 L9 4 L9.5 7 L8 8 C8.8 10 10 11.2 12 12 L13 10.5 L16 11 L16 14 C10 14.5 5.5 10 6 4 Z" fill="#111"/></svg>
        +94 5550 1287
      </li>
      <li>
        <svg viewBox="0 0 20 20" aria-hidden="true"><rect width="20" height="20" fill="var(--icon-bg)"/>
          <circle cx="10" cy="10" r="6" fill="none" stroke="#111" stroke-width="1.6"/>
          <path d="M4 10 H16 M10 4 C7 7 7 13 10 16 C13 13 13 7 10 4" fill="none" stroke="#111" stroke-width="1.2"/></svg>
        www.tallpinecomputing.com
      </li>
      <li>
        <svg viewBox="0 0 20 20" aria-hidden="true"><rect width="20" height="20" fill="var(--icon-bg)"/>
          <path d="M10 3 C6.7 3 5 5.4 5 8 C5 11 10 17 10 17 C10 17 15 11 15 8 C15 5.4 13.3 3 10 3 Z" fill="#111"/>
          <circle cx="10" cy="8" r="2" fill="var(--icon-bg)"/></svg>
        4210 Cedar Row, Langley, BC
      </li>
    </ul>
  </section>

  <section class="card card--back">
    <div class="fish-mark" role="img" aria-label="Cartoon fish mascot illustration"></div>
    <div class="brand-name">Tall Pine Computing</div>
  </section>

</div>
</body>
</html>
```